Sci Fi/ Secret Agent Author needs website design!

My name is Lark Whitby and I am an author. I require a site that can provide information about myself and my books and other works.

I would like it to have a Home, blog function, (about the) books/series section so people can visit another section and read about each individual book that's going to be released. A resources page, a Store, social media links and ability to load/embed videos from clipvane and other.

I write mild scifi/thriller/conspiracy/secret government type novels. -At the moment-. The series follows a strong female lead that is an agent with a secret organisation in a classified military installation.

The theme would be professional yet possibly show this element.

/military fiction/thriller/fantasy/Sci fi/ femme-fatal, readers. Mostly females, age 18-60
Novel readers

5+ page

• Would like designers to follow brief. :)
• My budget includes all the pages I will need;
• eg home, blog, resources, store, ability to pay with coinpouch and Credit Cards
• , ability to have trailers from clipvane etc. Must have links to the social media mentioned in the brief.
• use of the colours I have suggested. electric/indigo purple, fuschia highlights , dark greys
• as I will possibly base branding for social media ETC on the look of your website design and colour scheme.
• Ability for trailer on front page??
• Should not be too cluttered. (But I am open to all ideas)

```html
<!DOCTYPE html>
<html lang="en">
<head>
<meta charset="utf-8">
<title>Lark Whitby — Author</title>
<link rel="stylesheet" href="https://fonts.googleapis.com/css2?family=Tinos&family=Vollkorn:wght@400;600&family=Open+Sans:wght@400;600;700&display=swap">
<style>
:root{
  --nav-top:#7a22c9;
  --nav-bottom:#4d0e96;
  --nav-active:#3a0a72;
  --indigo:#2c0a6b;
  --electric:#5a10b4;
  --electric-dark:#460a91;
  --fuchsia:#b03ad8;
  --hero-dark:#241830;
  --hero-mid:#3b2a4c;
  --news-bg:#3a2a4a;
  --news-field:#4a3a5c;
  --ink:#1c1c1c;
  --body-text:#444;
  --muted-line:#d6d6d6;
  --blog-bg:#ebebed;
  --white:#fff;
  --chip-blue:#3b5b9e;
  --chip-sky:#27a0e6;
  --chip-violet:#5b7fd6;
  --chip-rose:#cc2040;
  --chip-red:#e01f1f;
}
*{box-sizing:border-box;margin:0;padding:0}
html,body{width:1200px;height:3220px;overflow:hidden}
body{position:relative;background:var(--white);font-family:"Open Sans",Arial,sans-serif;color:var(--ink)}
.abs{position:absolute}

/* navigation */
.site-nav{left:0;top:0;width:1200px;height:43px;background:linear-gradient(var(--nav-top),var(--nav-bottom))}
.site-nav a{position:absolute;top:0;height:43px;line-height:43px;text-align:center;color:var(--white);font-size:13px;text-decoration:none;border-right:1px solid rgba(255,255,255,.18)}
.site-nav a.is-active{background:var(--nav-active)}

/* header */
.brand{font-family:"Tinos","Times New Roman",serif;font-size:62px;letter-spacing:7px;color:var(--ink);line-height:1}
.follow{display:flex;align-items:center;gap:10px;font-size:10px;font-weight:600;color:var(--ink)}
.follow .net{display:flex;align-items:center;gap:4px;font-size:11px;font-weight:400}
.follow .dot{width:12px;height:12px;border-radius:50%;display:inline-block}

/* hero */
.hero{left:0;top:150px;width:1200px;height:570px;background:radial-gradient(ellipse at 70% 30%,var(--hero-mid),var(--hero-dark) 70%)}
.hero-book{left:146px;top:54px;width:478px;height:462px;background:linear-gradient(135deg,#0f2447,#163c66 55%,#0b2a3f);border-radius:6px}
.hero-frame{left:623px;top:129px;width:423px;height:296px;border:3px solid rgba(255,255,255,.55)}
.hero-title{left:670px;top:168px;font-family:"Tinos",serif;font-size:50px;color:var(--white)}
.hero-text{left:670px;top:236px;width:360px;font-size:17px;line-height:27px;color:#eee}
.btn{background:var(--electric);color:var(--white);text-align:center;text-transform:uppercase}
.hero-btn{left:670px;top:322px;width:185px;height:46px;line-height:46px;font-family:"Tinos",serif;font-size:19px}
.hero-arrow{top:253px;width:54px;height:54px;border:2px solid var(--white);border-radius:50%}

/* trailer */
.trailer{left:17px;top:736px;width:1166px;height:432px;background:linear-gradient(90deg,#1d1a1c,#5a4c48 40%,#2a2526 70%,#171516)}
.play{left:556px;top:157px;width:86px;height:86px;border-radius:50%;background:var(--electric);border:3px solid rgba(255,255,255,.7)}
.controls{left:294px;top:402px;width:580px;height:26px;background:rgba(90,16,180,.55);display:flex;align-items:center;gap:10px;padding:0 10px;font-size:11px;color:var(--white)}
.controls .track{flex:1;height:3px;background:rgba(255,255,255,.7)}

/* section headings */
.section-title{left:0;width:1200px;text-align:center;font-family:"Vollkorn",serif;font-size:39px;letter-spacing:7px;color:var(--indigo)}
.section-rule{left:561px;width:78px;height:3px;background:var(--fuchsia)}

/* books */
.book{top:1396px;height:343px;box-shadow:6px 6px 14px rgba(0,0,0,.25)}
.book-label{top:1776px;width:206px;border-top:2px solid var(--muted-line);padding-top:14px;text-align:center;font-family:"Vollkorn",serif;font-size:16px;letter-spacing:3px;color:var(--electric)}

/* blog */
.blog-band{left:0;top:1883px;width:1200px;height:646px;background:var(--blog-bg)}
.post{top:2061px;width:296px;height:387px;background:var(--white);border-radius:0 0 50% 50%/0 0 22px 22px;overflow:hidden;text-align:center}
.post-photo{width:296px;height:219px}
.post-date{left:245px;top:150px;width:43px;height:60px;background:#8c8c8c;color:var(--white);font-size:9px;line-height:1.1;padding-top:6px;font-weight:700}
.post-date b{display:block;font-size:20px}
.post-title{margin:34px 20px 0;font-size:13px;font-weight:700;text-transform:uppercase;line-height:19px}
.post-text{margin:10px 34px 0;font-size:11px;line-height:16px;color:var(--body-text)}
.post-btn{display:inline-block;margin-top:12px;width:97px;height:28px;line-height:28px;font-size:11px;font-weight:700}

/* newsletter */
.newsletter{left:133px;top:2602px;width:934px;height:303px;background:var(--news-bg)}
.news-book{left:167px;top:2576px;width:355px;height:344px;background:linear-gradient(135deg,#0f2447,#163c66 55%,#0b2a3f);border-radius:6px;box-shadow:10px 12px 20px rgba(0,0,0,.35)}
.news-title{left:541px;top:2656px;font-family:"Tinos",serif;font-size:29px;color:var(--white)}
.field{top:2720px;width:226px;height:50px;background:var(--news-field);border:1px solid rgba(255,255,255,.1);color:#ddd;font-size:11px;line-height:50px;padding-left:20px}
.signup{left:882px;top:2793px;width:138px;height:50px;line-height:50px;font-size:19px;font-weight:700}

/* footer */
.footer-brand{left:0;top:2955px;width:1200px;text-align:center}
.footer-follow{left:0;top:3068px;width:1200px;justify-content:center}
.footer-rule{left:461px;top:3124px;width:280px;height:1px;background:var(--muted-line)}
.copyright{left:0;top:3148px;width:1200px;text-align:center;font-size:12px}
</style>
</head>
<body>

<nav class="abs site-nav">
  <a href="#" class="is-active" style="left:135px;width:95px">Home</a>
  <a href="#" style="left:230px;width:214px">About the book</a>
  <a href="#" style="left:444px;width:194px">Resources</a>
  <a href="#" style="left:638px;width:152px">Store</a>
  <a href="#" style="left:790px;width:155px">Blog</a>
  <a href="#" style="left:945px;width:171px;border-right:0">Contact us</a>
</nav>

<header>
  <div class="abs brand" style="left:133px;top:64px">Lark Whitby</div>
  <div class="abs follow" style="left:700px;top:88px">
    <span>FOLLOW US ON :</span>
    <span class="net"><i class="dot" style="background:var(--chip-blue)"></i>facelink</span>
    <span class="net"><i class="dot" style="background:var(--chip-sky)"></i>chirpline</span>
    <span class="net"><i class="dot" style="background:var(--chip-violet)"></i>snapgrid</span>
    <span class="net"><i class="dot" style="background:var(--chip-rose)"></i>pinmoss</span>
    <span class="net"><i class="dot" style="background:var(--chip-red)"></i>clipvane</span>
  </div>
</header>

<section class="abs hero">
  <div class="abs hero-book" role="img" aria-label="Scifi book cover by Lark Whitby, blue glowing network on dark navy"></div>
  <div class="abs hero-frame"></div>
  <h1 class="abs hero-title" style="font-weight:400">Scifi</h1>
  <p class="abs hero-text">There are many variations of passages of Lorem Ipsum available.</p>
  <div class="abs btn hero-btn">Read more &#9656;</div>
  <div class="abs hero-arrow" style="left:44px">
    <svg width="50" height="50" viewBox="0 0 50 50"><path d="M28 17 L20 25 L28 33" stroke="#fff" stroke-width="2.5" fill="none"/></svg>
  </div>
  <div class="abs hero-arrow" style="left:1098px">
    <svg width="50" height="50" viewBox="0 0 50 50"><path d="M22 17 L30 25 L22 33" stroke="#fff" stroke-width="2.5" fill="none"/></svg>
  </div>
</section>

<section class="abs trailer" role="img" aria-label="Book trailer video still: a woman writing at a desk in a dim room by a window">
  <div class="abs play">
    <svg width="80" height="80" viewBox="0 0 80 80"><path d="M32 24 L56 40 L32 56 Z" fill="#fff"/></svg>
  </div>
  <div class="abs controls">
    <svg width="10" height="12" viewBox="0 0 10 12"><path d="M0 0 L10 6 L0 12 Z" fill="#fff"/></svg>
    <span class="track"></span>
    <span>3:50</span>
    <svg width="14" height="12" viewBox="0 0 14 12"><path d="M0 4 H4 L8 0 V12 L4 8 H0 Z" fill="#fff"/></svg>
    <svg width="16" height="12" viewBox="0 0 16 12"><rect x="1" y="1" width="14" height="10" fill="none" stroke="#fff" stroke-width="1.5"/></svg>
  </div>
</section>

<h2 class="abs section-title" style="top:1230px;font-weight:400">OUR BOOKS</h2>
<div class="abs section-rule" style="top:1309px"></div>

<div class="abs book" style="left:125px;width:208px;background:linear-gradient(150deg,#0f2447,#1a4b78 60%,#0b2a3f)" role="img" aria-label="Scifi book cover by Lark Whitby"></div>
<div class="abs book" style="left:369px;width:189px;background:linear-gradient(160deg,#3a3a3a,#9a9a9a 50%,#2a2a2a)" role="img" aria-label="Thriller book cover by Lark Whitby"></div>
<div class="abs book" style="left:616px;width:193px;background:linear-gradient(170deg,#f0f0f0,#111 45%,#000)" role="img" aria-label="Secret Agent book cover by Lark Whitby"></div>
<div class="abs book" style="left:867px;width:206px;background:linear-gradient(#d8332f,#c6262a)" role="img" aria-label="Conspiracy book cover by Lark Whitby"></div>

<div class="abs book-label" style="left:126px">Scifi</div>
<div class="abs book-label" style="left:370px">Thriller</div>
<div class="abs book-label" style="left:614px">Secret Agent</div>
<div class="abs book-label" style="left:867px">Conspiracy</div>

<section class="abs blog-band"></section>
<h2 class="abs section-title" style="top:1930px;font-weight:400">OUR BLOG</h2>
<div class="abs section-rule" style="top:2000px"></div>

<article class="abs post" style="left:133px">
  <div class="post-photo" role="img" aria-label="Couple sitting under a tree at sunset" style="background:linear-gradient(135deg,#f3b24a,#a9582a 55%,#3a2a1a)"></div>
  <div class="abs post-date">MAY<b>26</b>2017</div>
  <h3 class="post-title">Contrary to popular<br>belief lorem ipsum</h3>
  <p class="post-text">page editors now use Lorem Ipsum as their default model text, and a search</p>
  <div class="btn post-btn">Read more</div>
</article>

<article class="abs post" style="left:453px">
  <div class="post-photo" role="img" aria-label="Reading a book with a cup of coffee" style="background:linear-gradient(135deg,#d9d4cc,#9c8c7a 55%,#5a6a6a)"></div>
  <div class="abs post-date">MAY<b>26</b>2017</div>
  <h3 class="post-title">Lorem ipsum is simply dummy</h3>
  <p class="post-text">If you are going to use a passage of Lorem Ipsum, you need to be sure there isn't</p>
  <div class="btn post-btn">Read more</div>
</article>

<article class="abs post" style="left:775px">
  <div class="post-photo" role="img" aria-label="Reader studying a book at a desk beside shelves" style="background:linear-gradient(135deg,#c9b08a,#e8e2d8 50%,#7a8a9a)"></div>
  <div class="abs post-date">MAY<b>26</b>2017</div>
  <h3 class="post-title">It is a long established fact</h3>
  <p class="post-text">page editors now use Lorem Ipsum as their default model text, and a search</p>
  <div class="btn post-btn">Read more</div>
</article>

<section class="abs newsletter"></section>
<div class="abs news-book" role="img" aria-label="Scifi book cover by Lark Whitby"></div>
<h2 class="abs news-title" style="font-weight:400">NEWSLETTER SIGNUP!</h2>
<div class="abs field" style="left:545px">NAME</div>
<div class="abs field" style="left:794px">E MAIL ID</div>
<div class="abs btn signup">Signup</div>

<footer>
  <div class="abs brand footer-brand">Lark Whitby</div>
  <div class="abs follow footer-follow" style="display:flex">
    <span>FOLLOW US ON :</span>
    <span class="net"><i class="dot" style="background:var(--chip-blue)"></i>facelink</span>
    <span class="net"><i class="dot" style="background:var(--chip-sky)"></i>chirpline</span>
    <span class="net"><i class="dot" style="background:var(--chip-violet)"></i>snapgrid</span>
    <span class="net"><i class="dot" style="background:var(--chip-rose)"></i>pinmoss</span>
    <span class="net"><i class="dot" style="background:var(--chip-red)"></i>clipvane</span>
  </div>
  <div class="abs footer-rule"></div>
  <p class="abs copyright">Copyrights @ 2017 All Rights Reserved</p>
</footer>

</body>
</html>
```